Quorbelline.io - Please redesign to make it look better from current design

We already have the current website, that you can access but we think it can improve from current version.
Quorbelline is a cryptocurrency hedge fund that allow you to participate in the hedge fund with cryptocurrency such as eth.
At current phase, we are doing an ICO, then we want to make sure that the website it looks professional, beautiful and trustable enough for investors after looking at our website.
Target Market(s)
Investors
Industry/Entity Type
Investment
Coding
Coded - Design and coding required
Number of Pages Required
1 page
Look and feel
Each slider illustrates characteristics of the customer's brand and the style your logo design should communicate.

```html
<!DOCTYPE html>
<html lang="en">
<head>
<meta charset="utf-8">
<title>Quorbelline.io — Digital Asset Management</title>
<link rel="stylesheet" href="https://fonts.googleapis.com/css2?family=Montserrat:wght@400;500;600;700&display=swap">
<style>
  :root {
    --header-bg: #e9f0f7;
    --brand: #0b3f91;
    --brand-mid: #1a5fb0;
    --accent: #1d7bc0;
    --text: #2d2d2d;
    --muted: #555;
    --white: #ffffff;
    --footer-bg: #0a4fa0;
    --rule: #dcdcdc;
  }
  * { box-sizing: border-box; margin: 0; padding: 0; }
  html, body { width: 668px; height: 1200px; overflow: hidden; background: var(--white); }
  body { position: relative; font-family: "Montserrat", Arial, sans-serif; color: var(--text); }
  .abs { position: absolute; }

  .site-header { position: absolute; left: 0; top: 0; width: 668px; height: 59px; background: var(--header-bg); }
  .brand { position: absolute; left: 58px; top: 16px; display: flex; align-items: center; gap: 6px; }
  .brand-dot { width: 22px; height: 22px; border-radius: 50%; background: var(--brand); }
  .brand-name { font-size: 12px; font-weight: 600; color: var(--brand); }
  .main-nav { position: absolute; top: 25px; left: 381px; display: flex; gap: 0; font-size: 8px; color: #222; }
  .main-nav span { margin-right: 15px; }
  .search-btn { position: absolute; left: 591px; top: 19px; width: 22px; height: 22px; border-radius: 50%; background: var(--brand); }

  .hero { position: absolute; left: 0; top: 59px; width: 668px; height: 307px;
    background: linear-gradient(120deg, #6d6258 0%, #8a7e72 30%, #5b6670 60%, #7b8790 100%); }
  .hero-shade { position: absolute; inset: 0; background: rgba(40,45,60,0.35); }
  .hero-title { position: absolute; top: 121px; width: 100%; text-align: center; color: var(--white); font-size: 17px; font-weight: 500; letter-spacing: 0.5px; }
  .hero-sub { position: absolute; top: 142px; width: 100%; text-align: center; color: var(--white); font-size: 11px; }
  .hero-text { position: absolute; top: 159px; left: 174px; width: 320px; text-align: center; color: var(--white); font-size: 6.6px; line-height: 12px; }
  .btn { position: absolute; background: var(--brand-mid); color: var(--white); font-size: 6.5px; font-weight: 700; text-align: center; border-radius: 2px; }
  .hero .btn { left: 300px; top: 197px; width: 68px; height: 21px; line-height: 21px; }
  .dots { position: absolute; top: 266px; left: 316px; display: flex; gap: 4px; }
  .dots i { width: 5px; height: 5px; border-radius: 50%; background: rgba(255,255,255,0.6); display: block; }
  .dots i.on { background: var(--white); }

  .section-title { position: absolute; width: 100%; text-align: center; font-size: 12px; color: var(--accent); font-weight: 500; }
  .definition-text { position: absolute; left: 88px; top: 405px; width: 492px; text-align: center; font-size: 6.6px; line-height: 14.4px; color: var(--text); }
  .rule { position: absolute; left: 55px; top: 508px; width: 558px; height: 1px; background: var(--rule); }

  .member { position: absolute; top: 567px; width: 150px; text-align: center; }
  .avatar { width: 60px; height: 60px; border-radius: 50%; margin: 0 auto; }
  .member-name { margin-top: 8px; font-size: 9px; color: var(--accent); font-weight: 500; }
  .member-role { margin-top: 1px; font-size: 6.5px; font-style: italic; color: var(--accent); }
  .member-bio { margin-top: 5px; font-size: 5.6px; line-height: 11.5px; color: var(--text); height: 80px; }
  .member .btn { position: relative; display: inline-block; width: 52px; height: 17px; line-height: 17px; font-size: 5.5px; }

  .process { position: absolute; left: 0; top: 790px; width: 668px; height: 250px;
    background: radial-gradient(ellipse at 55% 50%, #8fc4e0 0%, #5ea6cf 45%, #3f8cbd 100%); }
  .process-title { position: absolute; top: 24px; width: 100%; text-align: center; color: var(--white); font-size: 11.5px; }
  .process-underline { position: absolute; top: 39px; left: 324px; width: 20px; height: 1.5px; background: var(--white); }
  .process-col { position: absolute; top: 100px; width: 230px; color: var(--white); }
  .process-col h3 { font-size: 11.5px; font-weight: 700; margin-bottom: 10px; }
  .process-col p { font-size: 5.9px; line-height: 11.5px; text-align: justify; }

  .info-title { position: absolute; top: 1062px; width: 100%; text-align: center; font-size: 11.5px; font-weight: 700; color: var(--accent); }
  .download { position: absolute; left: 270px; top: 1084px; width: 128px; height: 22px; line-height: 22px; background: var(--brand-mid); color: var(--white); font-size: 9.5px; text-align: center; border-radius: 2px; }

  .site-footer { position: absolute; left: 0; top: 1132px; width: 668px; height: 68px; background: var(--footer-bg); color: var(--white); }
  .address { position: absolute; left: 80px; top: 14px; width: 260px; font-size: 5.7px; line-height: 11px; }
  .pin { position: absolute; left: 66px; top: 15px; }
  .socials { position: absolute; left: 80px; top: 40px; display: flex; gap: 5px; }
  .socials i { width: 14px; height: 14px; display: block; border-radius: 1px; }
  .footer-nav { position: absolute; left: 411px; top: 17px; font-size: 7.4px; display: flex; }
  .footer-nav span { margin-right: 16px; }
  .copyright { position: absolute; left: 480px; top: 35px; font-size: 5.7px; }
</style>
</head>
<body>
  <header class="site-header">
    <div class="brand"><span class="brand-dot"></span><span class="brand-name">Quorbelline</span></div>
    <nav class="main-nav"><span>Home</span><span>About</span><span>Team</span><span>Process</span><span>Contact Us</span></nav>
    <div class="search-btn">
      <svg width="22" height="22" viewBox="0 0 22 22"><circle cx="10" cy="10" r="3" fill="none" stroke="#fff" stroke-width="1.3"/><line x1="12.2" y1="12.2" x2="14.5" y2="14.5" stroke="#fff" stroke-width="1.3"/></svg>
    </div>
  </header>

  <section class="hero" role="img" aria-label="Photo of a person working on a laptop at a desk">
    <div class="hero-shade"></div>
    <h1 class="hero-title">QUORBELLINE</h1>
    <div class="hero-sub">Digital Asset Management</div>
    <p class="hero-text">Quorbelline enable companies and investors to facilities business operation in modern digital world, including asset management on hedge fund strategy model.</p>
    <div class="btn">LEARN MORE</div>
    <div class="dots"><i></i><i></i><i class="on"></i><i></i></div>
  </section>

  <h2 class="section-title" style="top:387px">Definition</h2>
  <p class="definition-text">Quorbelline process and manages on hedge fund strategy models which invests in a diversified portfolio of blockchain tokens. Blockchain tokens are emerging which add a monetary incentive layer to p2p protocols and facilitate equity crowdfunding that anyone in the world can participate in. This means open source software developers can monetize their networks at the protocol level and users of the network are the equity owners of the network. For this conditions, returns will go to holders of the tokens.</p>
  <div class="btn" style="left:300px;top:473px;width:68px;height:21px;line-height:21px">READ MORE</div>
  <div class="rule"></div>

  <h2 class="section-title" style="top:527px">Executive Team</h2>

  <div class="member" style="left:88px">
    <div class="avatar" role="img" aria-label="Portrait of the director" style="background:#6b5a50"></div>
    <div class="member-name">Dorian Velcamp</div>
    <div class="member-role">Director</div>
    <p class="member-bio">As a hedge fund manager. Velcamp is the Chief Executive Officer of Brindlefield Capital LLC, an investment manager of Ashcombe Steel Fund SP (Long-Short Equity Fund, investing in U.S. Stock Market) and Kireno Apex Fund (Managed Futures Fund, focusing in Japanese Futures Market) Both based in Tokyo.</p>
    <div class="btn">READ MORE</div>
  </div>

  <div class="member" style="left:259px">
    <div class="avatar" role="img" aria-label="Portrait of the technical advisor" style="background:#b7bfa8"></div>
    <div class="member-name">Tavin Rosk</div>
    <div class="member-role">Technical advisor</div>
    <p class="member-bio">Rosk has various experienced on cryptocurrency and blockchain technology. He created what was the world's 4th most valuable cryptocurrency in February 2014. He is also the world's first person to implement stealth addresses in ZN-Wallets, improving cryptocurrency anonymity</p>
    <div class="btn">READ MORE</div>
  </div>

  <div class="member" style="left:431px">
    <div class="avatar" role="img" aria-label="Portrait of the marketing consultant" style="background:#6a2e24"></div>
    <div class="member-name">Kelvar Ostrinde</div>
    <div class="member-role">Marketing Consultant</div>
    <p class="member-bio">Ostrinde embeds a decade of experience in brand building, strategic planning, and marketing communication across the global agencies, such as Marrowgate Group, Velto, Lenhart Brill, Sorimachi. His seasoned specialty focuses on exploring a new market insight to formulate disruptive strategies</p>
    <div class="btn">READ MORE</div>
  </div>

  <section class="process" role="img" aria-label="Blue-toned photo of an open hand holding a glowing cross symbol">
    <h2 class="process-title">Process</h2>
    <div class="process-underline"></div>
    <div class="process-col" style="left:90px">
      <h3>HEDGE FUND MODEL</h3>
      <p>Quorbelline run on closed-end fund (CEF) model which offers its shares to investors and utilize the fund to speculate and invest in the innovative blockchain tokens. Quorbelline will charge an upfront annual operation fee 4% of the money raised during the ICO. After that, the fund will charge a quarterly performance of 50% on the net profit made.</p>
    </div>
    <div class="process-col" style="left:354px">
      <h3>NET PROFIT DISTRIBUTION</h3>
      <p>50 % of net profit is distributed to investors<br>0 - 5 % net profit &gt; 0% performance fee<br>5 - 10% net profit &gt; 5% performance fee<br>10-15 % net profit &gt; 13% performance fee<br>&gt; 15% net profit &gt; 15% performance fee<br>The remainder (50% minus performance fee, so at least 35%) is reinvested</p>
    </div>
  </section>

  <h2 class="info-title">FOR MORE INFORMATION</h2>
  <div class="download">Download Whitepaper</div>

  <footer class="site-footer">
    <svg class="pin" width="7" height="9" viewBox="0 0 7 9"><path d="M3.5 0C1.6 0 0 1.5 0 3.4 0 5.8 3.5 9 3.5 9S7 5.8 7 3.4C7 1.5 5.4 0 3.5 0z" fill="#fff"/><circle cx="3.5" cy="3.4" r="1.2" fill="#0a4fa0"/></svg>
    <p class="address">Suite 08-12, 9B/F., East Wing, Meridian Trade Centre, 42 Larkfield Road, Westbay, Harrowmere.</p>
    <div class="socials">
      <i style="background:#1a5fb0"></i><i style="background:#1da1f2"></i><i style="background:#d32222"></i><i style="background:#e53935"></i>
    </div>
    <nav class="footer-nav"><span>Home</span><span>About</span><span>Team</span><span>Process</span><span>Contact Us</span></nav>
    <div class="copyright">Copyrights © 2017 - All Rights Reserved</div>
  </footer>
</body>
</html>
```